Construction company business card

One side to be the logo with the company name, The other side I would like: (Tomas verbick) Project manager 41 barrow crescent hallam 52917306224783(03) 9703 2428Info@gudeljgroup.comAnd then maybe a couple dot points saying what we do:Construction (commercial & industrial) Civil construction

Anything else please contact me!
Maybe curved st one edge of the card

Target Market(s)

Older clientele

Industry/Entity Type

Construction Company

Contact Information for Business Card

Read above

Colors
3277b5
1b1b1b
9d9d9d

Requirements
Must have
• Use my logo on one side
Nice to have
• Read above
Should not have
• Read above

```html
<!DOCTYPE html>
<html lang="en">
<head>
<meta charset="utf-8">
<title>Stonefield Property Group – Business Card</title>
<link rel="stylesheet" href="https://fonts.googleapis.com/css2?family=Roboto:wght@400;500;700;900&display=swap">
<style>
  :root {
    --brand-blue: #2f5f96;
    --accent-blue: #3277b5;
    --ink: #1b1b1b;
    --grey: #9d9d9d;
    --card-face: #f1f1f1;
    --backdrop: #b9b9b9;
    --white: #ffffff;
  }
  * { box-sizing: border-box; margin: 0; padding: 0; }
  html, body {
    width: 1200px; height: 576px; overflow: hidden;
    background: var(--backdrop);
    font-family: "Roboto", Arial, sans-serif;
    color: var(--ink);
  }
  .canvas { position: relative; width: 1200px; height: 576px; }

  .card {
    position: absolute; top: 138px; height: 294px;
    background: var(--card-face);
    overflow: hidden;
    box-shadow: 0 3px 6px rgba(0,0,0,0.18);
  }
  .card--front { left: 82px; width: 485px; border-radius: 0 22px 0 0; }
  .card--back  { left: 602px; width: 482px; border-radius: 0 22px 0 22px; }

  /* Front */
  .brand { position: absolute; left: 0; width: 100%; text-align: center; color: var(--brand-blue); font-weight: 900; }
  .brand-mark {
    position: absolute; width: 84px; height: 84px; border-radius: 50%;
    background: var(--brand-blue);
  }
  .card--front .brand-mark { left: 200px; top: 48px; }
  .brand-name { font-size: 36px; line-height: 1; letter-spacing: 0.5px; }
  .brand-sub { font-size: 15px; letter-spacing: 4.6px; line-height: 1; margin-top: 4px; }
  .card--front .brand { top: 146px; }

  .web-line {
    position: absolute; top: 234px; left: 0; width: 100%;
    display: flex; justify-content: center; align-items: center; gap: 10px;
    font-size: 12.5px; color: var(--ink);
  }
  .web-line::before, .web-line::after {
    content: ""; width: 32px; height: 2px; background: var(--grey);
  }
  .services-line {
    position: absolute; top: 255px; left: 0; width: 100%;
    text-align: center; font-size: 13px; color: var(--ink);
  }
  .edge-band { position: absolute; bottom: 0; left: 0; width: 100%; height: 12px; display: flex; }
  .edge-band .grey { flex: 1; background: var(--grey); }
  .edge-band .blue { flex: 1; background: var(--brand-blue); }

  /* Back */
  .wave { position: absolute; top: 0; left: 0; }
  .card--back .brand-mark { left: 88px; top: 76px; }
  .card--back .brand { top: 188px; left: 20px; width: 222px; }
  .card--back .brand-name { font-size: 34px; }
  .card--back .brand-sub { font-size: 14px; letter-spacing: 4.2px; }

  .person { position: absolute; right: 30px; top: 20px; text-align: right; color: var(--white); }
  .person-name { font-size: 18px; font-weight: 700; line-height: 1.2; }
  .person-title { font-size: 12.5px; margin-top: 3px; }

  .services { position: absolute; right: 30px; top: 134px; text-align: right; color: var(--brand-blue); font-size: 12px; line-height: 19px; }

  .contacts { position: absolute; right: 22px; top: 189px; list-style: none; font-size: 12.5px; color: var(--ink); }
  .contacts li { display: flex; justify-content: flex-end; align-items: center; gap: 8px; height: 18px; }
  .contacts svg { width: 11px; height: 11px; fill: var(--brand-blue); }
  .contacts .address { padding-right: 19px; margin-top: 5px; }
</style>
</head>
<body>
<main class="canvas">

  <section class="card card--front" aria-label="Card front">
    <span class="brand-mark" aria-hidden="true"></span>
    <div class="brand">
      <div class="brand-name">STONEFIELD</div>
      <div class="brand-sub">PROPERTY GROUP</div>
    </div>
    <p class="web-line">www.stonefieldproperty.com</p>
    <p class="services-line">Construction (Commercial &amp; Industrial) Civil Construction</p>
    <div class="edge-band"><span class="grey"></span><span class="blue"></span></div>
  </section>

  <section class="card card--back" aria-label="Card back">
    <svg class="wave" width="482" height="294" viewBox="0 0 482 294" aria-hidden="true">
      <path d="M0 0 H482 V96 C400 82 330 22 210 16 C120 12 50 26 0 38 Z" fill="var(--brand-blue)"/>
      <path d="M0 66 C90 28 220 12 300 30 C380 48 430 98 482 104 V114 C420 108 360 64 290 48 C200 30 90 44 0 78 Z" fill="var(--grey)"/>
    </svg>

    <div class="person">
      <div class="person-name">Tomas Verbick</div>
      <div class="person-title">Project Manager</div>
    </div>

    <span class="brand-mark" aria-hidden="true"></span>
    <div class="brand">
      <div class="brand-name">STONEFIELD</div>
      <div class="brand-sub">PROPERTY GROUP</div>
    </div>

    <p class="services">Construction (Commercial &amp;<br>Industrial) Civil Construction</p>

    <ul class="contacts">
      <li>(73) 0622 4783
        <svg viewBox="0 0 24 24" aria-hidden="true"><path d="M6.6 10.8a15 15 0 0 0 6.6 6.6l2.2-2.2a1 1 0 0 1 1-.25 11.4 11.4 0 0 0 3.6.57 1 1 0 0 1 1 1V20a1 1 0 0 1-1 1A17 17 0 0 1 3 4a1 1 0 0 1 1-1h3.5a1 1 0 0 1 1 1c0 1.25.2 2.45.57 3.57a1 1 0 0 1-.25 1z"/></svg>
      </li>
      <li>(03) 9418 6573
        <svg viewBox="0 0 24 24" aria-hidden="true"><path d="M2 5h20v14H2z M2 5l10 8 10-8" fill="none" stroke="var(--brand-blue)" stroke-width="2.5"/></svg>
      </li>
      <li>Info@verbickgroup.com
        <svg viewBox="0 0 24 24" aria-hidden="true"><circle cx="12" cy="12" r="9.5" fill="none" stroke="var(--brand-blue)" stroke-width="2.5"/><path d="M2.5 12h19M12 2.5v19" stroke="var(--brand-blue)" stroke-width="2"/></svg>
      </li>
      <li class="address">41 Barrow Crescent Kestrel Park 5291</li>
    </ul>
  </section>

</main>
</body>
</html>
```